Fresh, modern, fun business card for pediatric dental practice

Need a business card for fresh, modern, fun pediatric dental practice

Clean look that matches our website's font and colors

We prefer the look of curved corners on business cards

Target Market(s)

parents (mothers) of young children, professionals, mid-high class

Industry/Entity Type

Dental

Contact Information for Business Card

Maplebrook Pediatric Dentistry
482 Quarry Lane
Suite 517
Cedarvale, PA 17999
717.555.0193
www.maplebrookkidsdental.example

Mei-Ran Tsai, DMD
Corinne Walbeck, DMD
(we are working on our email address, but we would like that on the card as well)

Font styles to use
Sans Serif

Requirements
Must have
• All info; we would also like to make cards for individual staff members
• colors from our website and color palatte, attatched
• use same font and design as website for branding
Nice to have
• clean, simple card that has a pop of color
• we would like to see a few designs with our tag line "where smiles get brighter"
• we are not sure if we want to have it on there or not
• we would like to see a few designs incorporating the ribbon graphic on our website where the word WELCOME is

```html
<!DOCTYPE html>
<html lang="en">
<head>
<meta charset="utf-8">
<title>Maplebrook Pediatric Dentistry – Business Card</title>
<link rel="stylesheet" href="https://fonts.googleapis.com/css2?family=Lato:wght@400;700&family=Raleway:wght@500&display=swap">
<style>
  :root {
    --sun: #f6b821;
    --berry: #c8168a;
    --ink: #2b2b2b;
    --card: #ffffff;
    --backdrop: #ece8e4;
  }
  html, body {
    margin: 0;
    width: 1200px;
    height: 900px;
    overflow: hidden;
    background: var(--backdrop);
  }
  .canvas {
    position: relative;
    width: 1200px;
    height: 900px;
  }
  .card {
    position: absolute;
    background: var(--card);
    border-radius: 18px;
    overflow: hidden;
    box-shadow: 0 4px 16px rgba(0,0,0,0.12);
  }
  .card--front {
    left: 178px; top: 74px;
    width: 588px; height: 364px;
  }
  .card--back {
    left: 391px; top: 508px;
    width: 562px; height: 347px;
  }
  .sun-band {
    position: absolute;
    left: 0; top: 0;
    width: 110px; height: 364px;
  }
  .doctors {
    position: absolute;
    right: 38px; top: 46px;
    margin: 0;
    text-align: right;
    font-family: "Raleway", sans-serif;
    font-weight: 500;
    font-size: 19.5px;
    line-height: 29px;
  }
  .doctors .doctor--first { color: var(--sun); display: block; }
  .doctors .doctor--second { color: var(--berry); display: block; }
  .contact {
    position: absolute;
    right: 38px; top: 166px;
    margin: 0; padding: 0;
    list-style: none;
    text-align: right;
    font-family: "Lato", sans-serif;
    font-size: 15px;
    line-height: 21.5px;
    color: var(--ink);
  }
  .contact li { display: flex; justify-content: flex-end; align-items: center; gap: 4px; }
  .contact svg { width: 11px; height: 11px; fill: var(--sun); }
  .practice {
    position: absolute;
    right: 38px; top: 268px;
    margin: 0;
    text-align: right;
    font-family: "Lato", sans-serif;
    font-style: normal;
    color: var(--ink);
    font-size: 15.5px;
    line-height: 21.5px;
  }
  .practice .practice-name { display: block; font-size: 17.5px; line-height: 24px; }
  .practice span { display: block; }
  .brand {
    position: absolute;
    left: 0; right: 0; top: 88px;
    text-align: center;
  }
  .brand-dot {
    display: block;
    width: 58px; height: 58px;
    margin: 0 auto 18px;
    border-radius: 50%;
    background: var(--sun);
  }
  .brand-name {
    margin: 0;
    font-family: "Lato", sans-serif;
    font-weight: 700;
    font-size: 34px;
    line-height: 40px;
    color: var(--sun);
  }
</style>
</head>
<body>
<main class="canvas">

  <section class="card card--front" aria-label="Business card, front">
    <svg class="sun-band" viewBox="0 0 110 364" aria-hidden="true">
      <path d="M0 0 H86 C78 40 92 70 84 110 C76 150 92 190 84 230 C76 270 92 310 84 364 H0 Z" fill="var(--sun)"/>
    </svg>

    <p class="doctors">
      <span class="doctor--first">Mei-Ran Tsai, DMD</span>
      <span class="doctor--second">Corinne Walbeck, DMD</span>
    </p>

    <ul class="contact">
      <li>717.555.0193
        <svg viewBox="0 0 12 12" aria-hidden="true"><path d="M1 4 C1 2 3 1 6 1 C9 1 11 2 11 4 L9 5 L8 3.6 C7 3.3 5 3.3 4 3.6 L3 5 Z M2 6 H10 L11 11 H1 Z"/></svg></li>
      <li>Mei-ran@maplebrookkidsdental.example
        <svg viewBox="0 0 12 12" aria-hidden="true"><path d="M1 2.5 H11 V9.5 H1 Z M1.8 3.2 L6 6.5 L10.2 3.2 Z" fill-rule="evenodd"/></svg></li>
      <li>Corinne@maplebrookkidsdental.example
        <svg viewBox="0 0 12 12" aria-hidden="true"><path d="M1 2.5 H11 V9.5 H1 Z M1.8 3.2 L6 6.5 L10.2 3.2 Z" fill-rule="evenodd"/></svg></li>
      <li>www.maplebrookkidsdental.example
        <svg viewBox="0 0 12 12" aria-hidden="true"><circle cx="6" cy="6" r="5"/></svg></li>
    </ul>

    <address class="practice">
      <span class="practice-name">Maplebrook Pediatric Dentistry</span>
      <span>482 Quarry Lane</span>
      <span>Suite 517 Cedarvale, PA 17999</span>
    </address>
  </section>

  <section class="card card--back" aria-label="Business card, back">
    <div class="brand">
      <span class="brand-dot" aria-hidden="true"></span>
      <p class="brand-name">maplebrook<br>pediatric dentistry</p>
    </div>
  </section>

</main>
</body>
</html>
```